Automotive eCommerce Business looking for a business card design

Looking for a clean and simple business card design. Our company name is "Brindle Auto" and we are a company specializing in the ecommerce sales of automotive parts, specifically for pick up trucks and large SUVs. Our company colours are red, black, and white.

Feel free to use the logo provided or create a new logo that you seem fit. Looking forward to your creative ideas!

Industry/Entity Type

Automotive

Contact Information for Business Card

We were thinking of a possibly two-sided design featuring just the logo and company name on one side, and personal information on the other side. Single sided designs will be considered as well.

Font styles to use
Serif
Sans Serif
Decorative

Colors
ec1f27
ffffff
000000

Requirements
Must have
• Space for employee's name, title, phone number and email address, along with the company address and website somewhere.

```html
<!DOCTYPE html>
<html lang="en">
<head>
<meta charset="utf-8">
<title>Brindle Auto Ltd. — Business Card</title>
<link rel="stylesheet" href="https://fonts.googleapis.com/css2?family=Cinzel:wght@400;500&family=Roboto:wght@400;500;700&display=swap">
<style>
  :root {
    --canvas-bg: #ececea;
    --card-bg: #f4f4f3;
    --brand-red: #a31d24;
    --band-grey: #4f5355;
    --text-grey: #555555;
    --white: #ffffff;
    --card-shadow: 0 3px 8px rgba(0,0,0,0.28);
  }
  * { margin: 0; padding: 0; box-sizing: border-box; }
  html, body { width: 1200px; height: 960px; overflow: hidden; }
  body { background: var(--canvas-bg); position: relative; font-family: "Roboto", Arial, sans-serif; }

  .card {
    position: absolute;
    left: 320px;
    width: 600px;
    background: var(--card-bg);
    border-radius: 20px;
    box-shadow: var(--card-shadow);
    overflow: hidden;
  }

  /* Front side */
  .card-front { top: 95px; height: 355px; text-align: center; }
  .front-mark {
    position: absolute; top: 128px; left: 0; width: 100%;
    display: flex; justify-content: center; align-items: center; gap: 14px;
  }
  .front-mark .mark-square { width: 34px; height: 34px; background: var(--brand-red); }
  .front-mark .mark-name {
    font-family: "Cinzel", Georgia, serif; font-weight: 500;
    font-size: 34px; color: var(--brand-red);
  }
  .front-company {
    position: absolute; top: 242px; left: 0; width: 100%;
    font-family: "Cinzel", Georgia, serif; font-weight: 500;
    font-size: 26px; color: var(--text-grey); letter-spacing: 0.5px;
  }
  .front-web {
    position: absolute; top: 304px; left: 0; width: 100%;
    font-size: 14px; color: var(--text-grey); letter-spacing: 5px;
  }

  /* Back side */
  .card-back { top: 493px; height: 342px; }
  .side-strip {
    position: absolute; left: 0; top: 0; width: 118px; height: 100%;
    background: var(--brand-red);
  }
  .side-strip .strip-band { height: 40px; background: var(--band-grey); }
  .strip-mark {
    position: absolute; top: 72px; left: 0; width: 100%;
    text-align: center; font-family: "Cinzel", Georgia, serif; font-weight: 500;
    font-size: 17px; line-height: 1.25; color: var(--white);
  }
  .contact-icons { position: absolute; left: 0; top: 0; width: 118px; height: 100%; }
  .contact-icons svg { position: absolute; left: 53px; width: 13px; height: 13px; fill: var(--white); }

  .back-company {
    position: absolute; left: 139px; top: 78px;
    font-family: "Cinzel", Georgia, serif; font-weight: 500;
    font-size: 26px; color: var(--text-grey); letter-spacing: 0.5px;
  }
  .contact-details {
    position: absolute; left: 139px; top: 176px;
    font-size: 14px; line-height: 19px; color: var(--text-grey);
  }
  .contact-details .address { margin-bottom: 9px; }
  .person {
    position: absolute; right: 35px; top: 272px; text-align: right;
  }
  .person .person-name { font-size: 19px; font-weight: 500; color: var(--brand-red); line-height: 24px; }
  .person .person-title { font-size: 14px; font-weight: 500; color: var(--text-grey); line-height: 20px; margin-top: 2px; }
</style>
</head>
<body>

  <section class="card card-front">
    <div class="front-mark">
      <span class="mark-square"></span>
      <span class="mark-name">Brindle Auto</span>
    </div>
    <h1 class="front-company">Brindle Auto Ltd.</h1>
    <p class="front-web">www.brindleauto.com</p>
  </section>

  <section class="card card-back">
    <div class="side-strip">
      <div class="strip-band"></div>
      <div class="strip-mark">Brindle<br>Auto</div>
      <div class="contact-icons">
        <svg viewBox="0 0 16 16" style="top:178px" aria-label="Address"><path d="M8 0a5.5 5.5 0 0 0-5.5 5.5C2.5 10 8 16 8 16s5.5-6 5.5-10.5A5.5 5.5 0 0 0 8 0zm0 8a2.5 2.5 0 1 1 0-5 2.5 2.5 0 0 1 0 5z"/></svg>
        <svg viewBox="0 0 16 16" style="top:226px" aria-label="Phone"><path d="M3.6 0.5l2.3 3.2-1.5 1.8c.9 2 2.6 3.8 4.6 4.8l1.8-1.5 3.2 2.3-1.2 3.2C7 14 2 9 0.5 1.8z"/></svg>
        <svg viewBox="0 0 16 16" style="top:245px" aria-label="Mobile"><path d="M4 0h8a1 1 0 0 1 1 1v14a1 1 0 0 1-1 1H4a1 1 0 0 1-1-1V1a1 1 0 0 1 1-1zm1 2v10h6V2zm3 11a1 1 0 1 0 0 2 1 1 0 0 0 0-2z"/></svg>
        <svg viewBox="0 0 16 16" style="top:264px" aria-label="Fax"><path d="M4 0h8v4H4zM1 5h14v7h-3v-3H4v3H1zm4 5h6v6H5z"/></svg>
        <svg viewBox="0 0 16 16" style="top:283px" aria-label="Email"><path d="M0 3h16v1.5L8 9 0 4.5zm0 3.2L8 10.5l8-4.3V13H0z"/></svg>
        <svg viewBox="0 0 16 16" style="top:302px" aria-label="Website"><path d="M8 0a8 8 0 1 0 0 16A8 8 0 0 0 8 0zm5.9 7h-2.5a12 12 0 0 0-1-4.6A6 6 0 0 1 13.9 7zM8 2c.8 1 1.3 2.9 1.4 5H6.6C6.7 4.9 7.2 3 8 2zM5.6 2.4A12 12 0 0 0 4.6 7H2.1a6 6 0 0 1 3.5-4.6zM2.1 9h2.5a12 12 0 0 0 1 4.6A6 6 0 0 1 2.1 9zM8 14c-.8-1-1.3-2.9-1.4-5h2.8c-.1 2.1-.6 4-1.4 5zm2.4-.4a12 12 0 0 0 1-4.6h2.5a6 6 0 0 1-3.5 4.6z"/></svg>
      </div>
    </div>

    <h2 class="back-company">Brindle Auto Ltd.</h2>

    <div class="contact-details">
      <p class="address">4120 Harrow Street<br>Fairbanks, Alaska 99701</p>
      <p>555 210 4471<br>555 318 2096<br>555 402 7753<br>sales@brindleauto.com<br>www.brindleauto.com</p>
    </div>

    <div class="person">
      <p class="person-name">MARK DALTON</p>
      <p class="person-title">CEO/FOUNDER</p>
    </div>
  </section>

</body>
</html>
```